Stationery and Business Card Design

We need stationary design for our new company lanternfold. Lanternfold is a company that provides city apartment rentals for tourists in Athens We need business cards, letterheads for A4 and A5 and envelopes for A4 A5. The design needs to be modern, friendly and corporate.

Target Market(s)

City Tourists

Industry/Entity Type

Tourism

```html
<!DOCTYPE html>
<html lang="en">
<head>
<meta charset="utf-8">
<title>Lanternfold Stationery</title>
<link href="https://fonts.googleapis.com/css2?family=Raleway:wght@400;500;700&family=Tinos:ital@0;1&display=swap" rel="stylesheet">
<style>
  :root {
    --brand: #8c0052;
    --brand-pale: #f3e3ec;
    --ink: #222;
    --ink-soft: #444;
    --paper: #fff;
    --backdrop: #545454;
  }
  * { box-sizing: border-box; margin: 0; padding: 0; }
  html, body { width: 1200px; height: 1200px; overflow: hidden; }
  body { background: var(--backdrop); position: relative; font-family: "Raleway", sans-serif; color: var(--ink); }

  .sheet { position: absolute; background: var(--paper); overflow: hidden; }

  .brand { display: flex; align-items: center; gap: 6px; color: var(--brand); font-family: "Raleway", sans-serif; font-weight: 400; line-height: 1; white-space: nowrap; }
  .brand-square { background: var(--brand); flex: none; }
  .brand--light { color: var(--paper); }
  .brand--light .brand-square { background: var(--paper); }

  .contact { font-family: "Raleway", sans-serif; color: var(--ink-soft); }
  .contact-row { display: flex; align-items: center; }
  .contact-row svg { flex: none; }

  /* A4 letterhead */
  .letter-a4 { left: 66px; top: 180px; width: 481px; height: 682px; }
  .letter-a4 .brand { position: absolute; left: 0; right: 0; top: 30px; justify-content: center; font-size: 21px; }
  .letter-a4 .brand-square { width: 18px; height: 18px; }
  .watermark { position: absolute; background: var(--brand-pale); opacity: .75; }
  .letter-a4 .watermark { left: 117px; top: 236px; width: 249px; height: 226px; }
  .letter-body { position: absolute; left: 60px; top: 104px; width: 359px; font-family: "Tinos", serif; font-size: 9.3px; line-height: 11.7px; color: var(--ink); text-align: justify; }
  .letter-body p { margin-bottom: 11.7px; }
  .letter-body .greeting { margin-bottom: 11px; }
  .letter-close { position: absolute; left: 60px; top: 380px; font-family: "Tinos", serif; font-size: 9.3px; line-height: 11.7px; }
  .signature { position: absolute; left: 60px; top: 406px; width: 76px; height: 26px; background: linear-gradient(90deg, #d9d9d9, #ececec); border-radius: 3px; }
  .signer { position: absolute; left: 60px; top: 437px; font-family: "Tinos", serif; font-size: 9.3px; }
  .letter-a4 .contact { position: absolute; left: 48px; top: 581px; font-size: 8.6px; line-height: 13.6px; }
  .letter-a4 .contact-row svg { width: 10px; height: 10px; margin-right: 17px; }
  .letter-a4 .contact .gap { height: 5px; }
  .band { position: absolute; left: 0; bottom: 0; width: 100%; }

  /* envelope */
  .envelope { left: 631px; top: 180px; width: 495px; height: 700px; }
  .envelope .flap { position: absolute; left: 0; top: 0; width: 495px; height: 96px; }
  .envelope .brand { position: absolute; left: 0; right: 0; top: 44px; justify-content: center; font-size: 19px; }
  .envelope .brand-square { width: 16px; height: 16px; }

  /* A5 letterhead */
  .letter-a5 { left: 578px; top: 260px; width: 495px; height: 701px; box-shadow: -2px 2px 6px rgba(0,0,0,.15); }
  .letter-a5 .brand { position: absolute; left: 45px; top: 75px; font-size: 20px; }
  .letter-a5 .brand-square { width: 17px; height: 17px; }
  .letter-a5 .contact { position: absolute; left: 45px; top: 125px; font-size: 6.2px; line-height: 10px; }
  .letter-a5 .contact-row svg { width: 7px; height: 7px; margin-right: 13px; }
  .letter-a5 .contact .gap { height: 3px; }
  .letter-a5 .watermark { left: 260px; top: 470px; width: 199px; height: 231px; background: linear-gradient(180deg, rgba(243,227,236,0), var(--brand-pale)); opacity: 1; }

  /* business cards */
  .card { top: 881px; width: 234px; height: 130px; }
  .card-front { left: 66px; }
  .card-back { left: 313px; }
  .card-front .brand { position: absolute; right: 20px; top: 42px; font-size: 14px; gap: 4px; }
  .card-front .brand-square { width: 11px; height: 11px; }
  .holder { position: absolute; left: 18px; top: 36px; }
  .holder-name { font-weight: 700; font-size: 7.6px; color: var(--ink); }
  .holder-role { font-size: 5.4px; color: var(--brand); margin-top: 2px; }
  .card-front .contact { position: absolute; left: 18px; top: 62px; font-size: 4.8px; line-height: 8.2px; }
  .card-front .contact-row svg { width: 5px; height: 5px; margin-right: 8px; }
  .card-front .contact .gap { height: 4px; }
  .card-back .brand { position: absolute; left: 0; right: 0; top: 56px; justify-content: center; font-size: 17px; gap: 5px; }
  .card-back .brand-square { width: 14px; height: 14px; }
</style>
</head>
<body>

<svg width="0" height="0" style="position:absolute">
  <defs>
    <symbol id="icon-phone" viewBox="0 0 12 12"><path d="M1 4.5c0-2 2-3 5-3s5 1 5 3l-2 .6-.5-1.6H3.5L3 5.1z M3 6h6l1 4H2z" fill="#8c0052"/><circle cx="6" cy="8" r="1.2" fill="#fff"/></symbol>
    <symbol id="icon-mobile" viewBox="0 0 12 12"><rect x="3.5" y="1" width="5" height="10" rx="1" fill="none" stroke="#8c0052" stroke-width="1.2"/></symbol>
    <symbol id="icon-mail" viewBox="0 0 12 12"><rect x="1" y="2.5" width="10" height="7" fill="none" stroke="#8c0052" stroke-width="1.2"/><path d="M1 2.5l5 4 5-4" fill="none" stroke="#8c0052" stroke-width="1.2"/></symbol>
    <symbol id="icon-web" viewBox="0 0 12 12"><circle cx="6" cy="6" r="4.8" fill="none" stroke="#8c0052" stroke-width="1.2"/><path d="M1.2 6h9.6M6 1.2c-2.4 3-2.4 6.6 0 9.6M6 1.2c2.4 3 2.4 6.6 0 9.6" fill="none" stroke="#8c0052" stroke-width=".9"/></symbol>
  </defs>
</svg>

<!-- A4 letterhead -->
<section class="sheet letter-a4">
  <div class="brand"><span class="brand-square"></span>Lanternfold</div>
  <div class="watermark"></div>
  <div class="letter-body">
    <p class="greeting">Gentlemen,</p>
    <p>Enclosed I have the honor to send you an article which I should be pleased if you would accept for the "Harbour Review". I am <em>desperately</em> pushed for money; and in the event of Mr. Ardley's liking the "Landscape-Garden", I would take it as an especial favor if you would mail me the amount due for it, so as to reach me here by the 21st, on which day I shall need it. Can you possibly oblige me in this? If you accept the paper I presume you will allow me your usual sum, whatever that is for similar contributions—but I set no price—leaving all to your own liberality. The piece will make 8 of your pages and rather more.</p>
    <p>Will you be kind enough to put the best possible interpretation upon my behavior while in Westbrook? You must have conceived a <em>queer</em> idea of me—but the simple truth is that Pellham would insist upon <em>the juleps</em>, and I knew not what I was either doing or saying. The Review of Corvin which I offered you was deficient in a 1/2 page of commencement, which I had written to supersede the old beginning, and which gave the article the character of a general and retrospective review. No wonder you did not take it—I would have been very much mortified if you had. I hope to see you at some future time, under better auspices.</p>
  </div>
  <div class="letter-close">In the meantime I remain<br>Yours very truly,</div>
  <div class="signature" role="img" aria-label="Handwritten signature"></div>
  <div class="signer">Elias Marlow</div>
  <div class="contact">
    <div>21 Orion Lane, Marlowvale</div>
    <div>Westbrook 0712</div>
    <div class="gap"></div>
    <div class="contact-row"><svg><use href="#icon-phone"/></svg>555 318 4402</div>
    <div class="contact-row"><svg><use href="#icon-mail"/></svg>info@lanternfoldapartments.com</div>
    <div class="contact-row"><svg><use href="#icon-web"/></svg>www.lanternfoldapartments.com</div>
  </div>
  <svg class="band" width="481" height="25" viewBox="0 0 481 25"><polygon points="0,17 481,17 481,25 0,25" fill="#8c0052"/><polygon points="320,0 481,0 481,25 310,25" fill="#8c0052"/></svg>
</section>

<!-- envelope -->
<section class="sheet envelope">
  <svg class="flap" viewBox="0 0 495 96"><path d="M0 0H495L465 83Q460 96 445 96H40L0 0Z" fill="#8c0052"/></svg>
  <div class="brand brand--light"><span class="brand-square"></span>Lanternfold</div>
</section>

<!-- A5 letterhead -->
<section class="sheet letter-a5">
  <div class="brand"><span class="brand-square"></span>Lanternfold</div>
  <div class="contact">
    <div>21 Orion Lane, Marlowvale</div>
    <div>Westbrook 0712</div>
    <div class="gap"></div>
    <div class="contact-row"><svg><use href="#icon-phone"/></svg>555 318 4402</div>
    <div class="contact-row"><svg><use href="#icon-mail"/></svg>info@lanternfoldapartments.com</div>
    <div class="contact-row"><svg><use href="#icon-web"/></svg>www.lanternfoldapartments.com</div>
  </div>
  <div class="watermark"></div>
</section>

<!-- business card front -->
<section class="sheet card card-front">
  <div class="holder">
    <div class="holder-name">Daniel Corbett</div>
    <div class="holder-role">President</div>
  </div>
  <div class="brand"><span class="brand-square"></span>Lanternfold</div>
  <div class="contact">
    <div>21 Orion Lane, Marlowvale</div>
    <div>Westbrook 0712</div>
    <div class="gap"></div>
    <div class="contact-row"><svg><use href="#icon-phone"/></svg>555 318 4402</div>
    <div class="contact-row"><svg><use href="#icon-mobile"/></svg>555 318 4404</div>
    <div class="contact-row"><svg><use href="#icon-mail"/></svg>info@lanternfoldapartments.com</div>
    <div class="contact-row"><svg><use href="#icon-web"/></svg>www.lanternfoldapartments.com</div>
  </div>
  <svg class="band" width="234" height="14" viewBox="0 0 234 14"><polygon points="0,10 234,10 234,14 0,14" fill="#8c0052"/><polygon points="130,0 234,0 234,14 123,14" fill="#8c0052"/></svg>
</section>

<!-- business card back -->
<section class="sheet card card-back">
  <div class="brand"><span class="brand-square"></span>Lanternfold</div>
</section>

</body>
</html>
```